Veldmark Supplies Business Card

Professional business card that stand out to our potential customers. Front and back with clean modern design

Industry/Entity Type

Oil and gas

Contact Information for Business Card

Name, address, website , office phone and cell number

Requirements
Must have
• Editable files for each employee

```html
<!DOCTYPE html>
<html lang="en">
<head>
<meta charset="utf-8">
<title>Veldmark Supplies Business Card</title>
<link rel="stylesheet" href="https://fonts.googleapis.com/css2?family=Arimo:wght@400;700&display=swap">
<style>
  :root {
    --stage: #3b3b3d;
    --brand-red: #ff0000;
    --brand-cyan: #16aed3;
    --paper: #ffffff;
  }
  * { margin: 0; padding: 0; box-sizing: border-box; }
  html, body { width: 1200px; height: 689px; overflow: hidden; background: var(--stage); }
  body { font-family: "Arimo", Arial, sans-serif; position: relative; }

  .card {
    position: absolute;
    top: 195px;
    width: 525px;
    height: 300px;
    border-radius: 18px;
    overflow: hidden;
  }
  .card--front { left: 45px; background: var(--brand-red); }
  .card--back { left: 630px; background: var(--paper); }

  .brand {
    position: absolute;
    display: flex;
    align-items: center;
    gap: 10px;
    font-weight: 700;
    letter-spacing: 1.5px;
    white-space: nowrap;
  }
  .brand__mark { display: block; }
  .card--front .brand {
    left: 50%; top: 50%; transform: translate(-50%, -50%);
    color: var(--paper); font-size: 26px;
  }
  .card--front .brand__mark { width: 22px; height: 22px; background: var(--paper); }
  .card--back .brand {
    left: 50%; top: 78px; transform: translateX(-50%);
    color: var(--brand-red); font-size: 19px;
  }
  .card--back .brand__mark { width: 16px; height: 16px; background: var(--brand-red); }

  .back__band {
    position: absolute; left: 0; right: 0; bottom: 0; height: 138px;
    background: var(--brand-red);
    border-top: 4px solid var(--brand-cyan);
  }
  .person {
    position: absolute; right: 290px; top: 28px;
    text-align: right; color: var(--paper);
  }
  .person__name { color: var(--brand-cyan); font-weight: 700; font-size: 22px; line-height: 1.1; }
  .person__title { font-size: 13px; margin-bottom: 6px; }
  .person__address { font-size: 13px; line-height: 1.35; }

  .band__divider {
    position: absolute; left: 250px; top: 26px; width: 1px; height: 86px;
    background: rgba(255,255,255,0.7);
  }
  .contacts {
    position: absolute; left: 266px; top: 28px;
    list-style: none; color: var(--paper); font-size: 13px;
  }
  .contacts li { display: flex; align-items: center; gap: 8px; line-height: 20px; }
  .contacts svg { width: 12px; height: 12px; flex: none; }
</style>
</head>
<body>

  <section class="card card--front" aria-label="Card front">
    <div class="brand"><span class="brand__mark"></span>VELDMARK SUPPLIES</div>
  </section>

  <section class="card card--back" aria-label="Card back">
    <div class="brand"><span class="brand__mark"></span>VELDMARK SUPPLIES</div>

    <div class="back__band">
      <div class="person">
        <p class="person__name">Aaron Vale</p>
        <p class="person__title">President</p>
        <p class="person__address">412 Juniper Road<br>Halden, Canada 20815</p>
      </div>

      <div class="band__divider"></div>

      <ul class="contacts">
        <li>
          <svg viewBox="0 0 12 12" aria-hidden="true"><path d="M2.5 1 4.5 1 5 3.6 3.8 4.6C4.5 6 6 7.5 7.4 8.2L8.4 7 11 7.5 11 9.5C11 10.3 10.3 11 9.5 11 5 11 1 7 1 2.5 1 1.7 1.7 1 2.5 1Z" fill="#fff"/></svg>
          555-210-4817
        </li>
        <li>
          <svg viewBox="0 0 12 12" aria-hidden="true"><rect x="3" y="0.8" width="6" height="10.4" rx="1" fill="none" stroke="#fff" stroke-width="1.2"/><circle cx="6" cy="9.4" r="0.7" fill="#fff"/></svg>
          555-376-9042
        </li>
        <li>
          <svg viewBox="0 0 12 12" aria-hidden="true"><rect x="0.8" y="2.3" width="10.4" height="7.4" fill="none" stroke="#fff" stroke-width="1.2"/><path d="M1 2.6 6 6.5 11 2.6" fill="none" stroke="#fff" stroke-width="1.2"/></svg>
          info@veldmarksupplies.com
        </li>
        <li>
          <svg viewBox="0 0 12 12" aria-hidden="true"><circle cx="6" cy="6" r="5" fill="none" stroke="#fff" stroke-width="1.2"/><ellipse cx="6" cy="6" rx="2.2" ry="5" fill="none" stroke="#fff" stroke-width="1"/><path d="M1 6H11" stroke="#fff" stroke-width="1"/></svg>
          www.veldmarksupplies.com
        </li>
      </ul>
    </div>
  </section>

</body>
</html>
```